PeakRoamJourneys

1. Can you describe what your company does?

Please find enclosed documents for your reference about our business doing.

2. Who are your target customers for the website?

Company Positioning: A comprehensive supplier of premier international sports travel and high-end event services.
Core Advantage: Exclusive international partnership resources and an Official Ticketing Assurance System.
Service Standard: One-Stop, High-Quality Service Solutions based on the "An once-in-a-lifetime experience" philosophy.

Our target customers for the website:
Mid-to-High-end Sports Enthusiasts
Corporate Clients
Sports Associations
Please kindly find enclosed for more details about our target customers, I think it's very important to make it clear to you.

3. Do you have an existing domain name / website address?

Yes, I have. I just applied for this new domain and it's totally a new website. www.peakroamjourneys.example

4. In addition to a Home Page, which other pages / sections would you like your website to have:
About Us
Contact Us , Office / Mailing Address
Sports Travel Products( Bucket Lists) : Globe Shield, Royal Quartet, Vantara Games, Football, Courtline League, Golf, Skiing, Hiking,Galas
Reviews/ Unforgettable Moments
FAQs
Any other page / section you would like: Here is the website for your reference, www.lanewander.example
For each of the pages / sections you’d like to have, please provide the text (and images, if available) you would like to include.
Please recommend 2-3 templates to me, and let me know what kind of text I will provide to every web pages.

5. Which of the below are features and functionalities your website will need:
Image Gallery
Videos
Contact Form
Maps
FAQs
6. Please provide the URLs for the social media profiles you'd like to link to the website.

Do you know Bright Lantern App?

Please let me know anything you need, thank you very much!

Have a good day!

Target Market(s)

Travel for the world-wide sports games and make an once-in-a-lifetime experience

Industry/Entity Type

sports and travel industry

Coding

Number of Pages Required

5+ page

Requirements
Must have
• our logo
Nice to have
• On the homepage, I’d like a banner-style section to prominently showcase the latest products.

```html
<!DOCTYPE html>
<html lang="en">
<head>
<meta charset="utf-8">
<title>PeakRoamJourneys — Your Global Sports Gateway</title>
<link rel="stylesheet" href="https://fonts.googleapis.com/css2?family=Oswald:wght@500;600&family=Poppins:wght@400;500;600&display=swap">
<style>
:root{
  --navy:#13308f;
  --navy-deep:#0d2a8a;
  --ink:#1d1d2b;
  --body:#3d3f4a;
  --mist:#e1e6f0;
  --line:#7f8fb6;
  --star:#f08a1c;
  --white:#fff;
}
*{box-sizing:border-box;margin:0;padding:0}
html,body{width:1200px;height:4918px;overflow:hidden}
body{font-family:"Poppins",sans-serif;color:var(--body);background:var(--white);position:relative}
.h{font-family:"Oswald",sans-serif;color:var(--navy);font-weight:600;letter-spacing:.2px}
.wrap{position:absolute;left:112px;width:976px}
.btn{display:inline-flex;align-items:center;gap:8px;background:var(--navy);color:var(--white);font-size:15px;font-weight:500;padding:0 22px;height:36px}
.btn svg{width:12px;height:12px}

/* header */
.site-header{position:absolute;top:0;left:0;width:1200px;height:85px;border-bottom:1px solid #e4e6ee;background:var(--white)}
.brand{position:absolute;left:112px;top:20px;font-size:32px;color:var(--navy)}
.nav{position:absolute;right:112px;top:32px;display:flex;gap:26px;font-size:15px;color:var(--ink)}
.nav .active{font-weight:600}

/* hero */
.hero{position:absolute;top:85px;left:0;width:1200px;height:515px;background:radial-gradient(ellipse at 70% 35%,#3a6fb0 0%,#1c3446 40%,#0e1a1c 75%),#102018}
.hero-photo{position:absolute;inset:0;background:linear-gradient(180deg,rgba(10,20,30,0) 50%,rgba(40,90,40,.85) 100%)}
.hero h1{position:absolute;left:112px;top:105px;font-family:"Oswald",sans-serif;font-size:56px;line-height:66px;color:var(--white);font-weight:600;letter-spacing:.3px}
.hero p{position:absolute;left:112px;top:255px;width:500px;font-size:17px;line-height:26px;color:var(--white)}
.hero .btn{position:absolute;left:112px;top:337px;background:var(--white);color:var(--navy);height:34px;font-size:14px}

/* intro */
.intro-title{position:absolute;top:676px;left:0;width:1200px;text-align:center;font-size:40px}
.intro-copy{top:772px;width:560px;font-size:14.5px;line-height:26px}
.intro-copy p+p{margin-top:12px}
.shoe{position:absolute;left:0;top:985px;width:440px;height:180px;background:linear-gradient(90deg,rgba(225,230,240,0) 0%,#eef1f7 55%,#e4e9f4 100%);border-radius:0 90px 60px 0}
.features{position:absolute;left:705px;top:776px;width:384px;height:388px;background:var(--mist);padding:36px 36px}
.feature{display:flex;gap:24px;margin-bottom:30px}
.feature .ic{flex:none;width:66px;height:66px;border-radius:50%;background:var(--navy);display:flex;align-items:center;justify-content:center}
.feature h3{font-size:17px;font-weight:500;color:var(--navy-deep);line-height:20px}
.feature p{font-size:13px;line-height:16px;margin-top:10px}
.rule{position:absolute;left:112px;width:976px;height:2px;background:var(--line)}

/* bucket list */
.band{position:absolute;left:0;width:1200px;background:var(--mist)}
.bucket-title{top:1328px;font-size:40px;line-height:48px;width:460px}
.bucket-note{position:absolute;left:617px;top:1340px;height:72px;border-left:3px solid #555;padding-left:16px;font-size:13.5px;line-height:25px;width:472px;color:var(--ink)}
.bucket{position:absolute;top:1467px;width:302px}
.bucket .photo{height:276px}
.bucket .label{margin-top:18px;height:44px;border:2px solid var(--line);background:var(--white);display:flex;align-items:center;justify-content:center;font-size:18px;font-weight:500;color:var(--navy-deep)}

.center-title{position:absolute;left:0;width:1200px;text-align:center;font-size:40px}
.center-copy{position:absolute;left:0;width:1200px;text-align:center;font-size:15px;line-height:26px}

/* testimonials */
.t-row{position:absolute;left:0;width:1200px;height:214px;overflow:hidden}
.card{position:absolute;top:0;width:305px;height:212px;border:2px solid #c3c9d9;border-radius:8px;background:var(--mist);padding:26px 22px}
.card h4{font-size:12.5px;font-weight:600;color:var(--ink)}
.stars{display:flex;gap:2px;margin:16px 0 12px}
.stars svg{width:13px;height:13px}
.card p{font-size:12.5px;line-height:21px}
.card .who{font-style:italic;font-weight:500;margin-top:16px;font-size:12px}

/* gallery */
.left-title{font-size:40px}
.left-copy{font-size:15px;line-height:26px}
.g{position:absolute}

/* faq */
.faq{position:absolute;width:474px;height:44px;border:2px solid var(--line);display:flex;align-items:center;justify-content:space-between;padding:0 18px;font-size:14.5px;color:var(--ink)}
.faq svg{width:12px;height:8px}

/* contact */
.field{position:absolute;left:112px;width:468px;height:38px;border:2px solid #9aa3bd;background:var(--white);font-size:13px;padding:8px 14px;color:#6c7080}
.info{position:absolute;left:657px;font-size:12px;line-height:18px;color:var(--ink)}
.info b{position:absolute;left:0;color:var(--navy);font-size:15px;font-weight:500}
.info span{display:block;margin-left:86px;width:250px}

/* footer */
.site-footer{position:absolute;top:4700px;left:0;width:1200px;height:218px;background:var(--navy-deep);color:var(--white);text-align:center}
.site-footer .brand-f{font-size:34px;color:var(--white);margin-top:42px}
.foot-nav{display:flex;justify-content:center;gap:30px;font-size:17px;margin-top:22px}
.foot-rule{width:976px;height:1px;background:rgba(255,255,255,.55);margin:20px auto 0}
.copy{font-size:12.5px;margin-top:16px}
</style>
</head>
<body>

<header class="site-header">
  <div class="brand h">PeakRoamJourneys</div>
  <nav class="nav">
    <span class="active">Home</span><span>About</span><span>Sports Travel Products</span><span>Reviews</span><span>News</span><span>Contact Us</span>
    <svg width="16" height="16" viewBox="0 0 16 16" fill="none" stroke="#1d1d2b" stroke-width="2"><circle cx="7" cy="7" r="5"/><path d="M11 11l4 4"/></svg>
  </nav>
</header>

<section class="hero" role="img" aria-label="Night-lit stadium with a football player striking the ball on the pitch">
  <div class="hero-photo"></div>
  <h1>Your Global Sports<br>Gateway</h1>
  <p>From the Globe Shield to the Vantara Games — live your dream moments in style.</p>
  <span class="btn"><svg viewBox="0 0 12 12" fill="none" stroke="currentColor" stroke-width="2"><path d="M1 1l5 5-5 5M6 1l5 5-5 5"/></svg>Explore Events</span>
</section>

<h2 class="intro-title h">Experience Sports Like Never Before</h2>
<div class="wrap intro-copy">
  <p>PeakRoamJourneys is a comprehensive supplier of premier international sports travel and high-end event services. We open the doors to the most exclusive events around the world — from the Globe Shield and the Vantara Games to the Pinecrest Classic and the Courtline Finals.</p>
  <p>Our exclusive global partnerships and Official Ticketing Assurance System guarantee your access to authentic, premium experiences with total peace of mind.</p>
</div>
<div class="shoe" role="img" aria-label="Single-line drawing of a running shoe"></div>

<aside class="features">
  <div class="feature">
    <div class="ic"><svg width="30" height="30" viewBox="0 0 30 30" fill="none" stroke="#fff" stroke-width="2.2"><rect x="5" y="9" width="20" height="14" rx="2"/><path d="M10 16l4 4 7-8"/></svg></div>
    <div><h3>Official Ticketing<br>Assurance</h3><p>100% verified and secured event access.</p></div>
  </div>
  <div class="feature">
    <div class="ic"><svg width="30" height="30" viewBox="0 0 30 30" fill="none" stroke="#fff" stroke-width="2.2"><path d="M5 15l6-6 5 4 5-5 5 5-9 10z"/></svg></div>
    <div><h3>Exclusive Global<br>Partnerships</h3><p>Trusted international network.</p></div>
  </div>
  <div class="feature">
    <div class="ic"><svg width="30" height="30" viewBox="0 0 30 30" fill="none" stroke="#fff" stroke-width="2.2"><rect x="6" y="10" width="18" height="14" rx="2"/><path d="M11 10V6h8v4M12 14v6M18 14v6"/></svg></div>
    <div><h3>Tailored Travel<br>Solutions</h3><p>Every detail designed around you.</p></div>
  </div>
</aside>

<div class="rule" style="top:1249px"></div>

<div class="band" style="top:1550px;height:1115px"></div>
<h2 class="wrap bucket-title h">Your Ultimate Sports Bucket List Awaits</h2>
<p class="bucket-note">From legendary stadiums to breathtaking venues, explore our curated collection of world-class sporting events and adventures.</p>

<div class="bucket" style="left:112px">
  <div class="photo" role="img" aria-label="Golden trophy displayed in a floodlit stadium" style="background:linear-gradient(180deg,#1d4f9a 0%,#2a5fa8 45%,#c9a640 62%,#2f7a2f 100%)"></div>
  <div class="label">Globe Shield</div>
</div>
<div class="bucket" style="left:450px">
  <div class="photo" role="img" aria-label="Tennis player lunging for a shot on a blue court" style="background:linear-gradient(160deg,#2f86d0 0%,#1f6fb8 100%)"></div>
  <div class="label">Royal Quartet Tennis</div>
</div>
<div class="bucket" style="left:787px">
  <div class="photo" role="img" aria-label="Basketball player dribbling on a hardwood court" style="background:linear-gradient(180deg,#4a4a4e 0%,#6b6560 55%,#8a5a36 100%)"></div>
  <div class="label">Courtline &amp; Football</div>
</div>
<span class="btn" style="position:absolute;left:489px;top:1843px;height:36px;font-size:14px"><svg viewBox="0 0 12 12" fill="none" stroke="currentColor" stroke-width="2"><path d="M1 1l5 5-5 5M6 1l5 5-5 5"/></svg>View All Experiences</span>

<h2 class="center-title h" style="top:1958px">Our Testimonials</h2>
<p class="center-copy" style="top:2030px">PeakRoamJourneys is a comprehensive supplier of premier international sports travel and high-end event services.<br>We open the doors to the most exclusive events around the world</p>

<svg width="0" height="0" style="position:absolute"><defs><path id="star" fill="#f08a1c" d="M5 0l1.5 3.2 3.5.4-2.6 2.4.7 3.5L5 7.8 1.9 9.5l.7-3.5L0 3.6l3.5-.4z"/></defs></svg>

<div class="t-row" style="top:2132px">
  <article class="card" style="left:-210px"><h4>Lorem ipsum dolor sit amet, consectetur</h4><div class="stars"><svg viewBox="0 0 10 10"><use href="#star"/></svg><svg viewBox="0 0 10 10"><use href="#star"/></svg><svg viewBox="0 0 10 10"><use href="#star"/></svg><svg viewBox="0 0 10 10"><use href="#star"/></svg><svg viewBox="0 0 10 10"><use href="#star"/></svg></div><p>“Lorem ipsum dolor sit amet, consectetur adipiscing elit, sed do eiusmod tempor inc ididunt ut labore et dolore magna aliqua.”</p><p class="who">-R. Hale, Linden, GA</p></article>
  <article class="card" style="left:128px"><h4>Lorem ipsum dolor sit amet, consectetur</h4><div class="stars"><svg viewBox="0 0 10 10"><use href="#star"/></svg><svg viewBox="0 0 10 10"><use href="#star"/></svg><svg viewBox="0 0 10 10"><use href="#star"/></svg><svg viewBox="0 0 10 10"><use href="#star"/></svg><svg viewBox="0 0 10 10"><use href="#star"/></svg></div><p>“Lorem ipsum dolor sit amet, consectetur adipiscing elit, sed do eiusmod tempor inc ididunt ut labore et dolore magna aliqua.”</p><p class="who">-R. Hale, Linden, GA</p></article>
  <article class="card" style="left:465px"><h4>Lorem ipsum dolor sit amet, consectetur</h4><div class="stars"><svg viewBox="0 0 10 10"><use href="#star"/></svg><svg viewBox="0 0 10 10"><use href="#star"/></svg><svg viewBox="0 0 10 10"><use href="#star"/></svg><svg viewBox="0 0 10 10"><use href="#star"/></svg><svg viewBox="0 0 10 10"><use href="#star"/></svg></div><p>“Lorem ipsum dolor sit amet, consectetur adipiscing elit, sed do eiusmod tempor inc ididunt ut labore et dolore magna aliqua.”</p><p class="who">-R. Hale, Linden, GA</p></article>
  <article class="card" style="left:802px"><h4>Lorem ipsum dolor sit amet, consectetur</h4><div class="stars"><svg viewBox="0 0 10 10"><use href="#star"/></svg><svg viewBox="0 0 10 10"><use href="#star"/></svg><svg viewBox="0 0 10 10"><use href="#star"/></svg><svg viewBox="0 0 10 10"><use href="#star"/></svg><svg viewBox="0 0 10 10"><use href="#star"/></svg></div><p>“Lorem ipsum dolor sit amet, consectetur adipiscing elit, sed do eiusmod tempor inc ididunt ut labore et dolore magna aliqua.”</p><p class="who">-R. Hale, Linden, GA</p></article>
  <article class="card" style="left:1139px"><h4>Lorem ipsum dolor sit amet, consectetur</h4><div class="stars"><svg viewBox="0 0 10 10"><use href="#star"/></svg><svg viewBox="0 0 10 10"><use href="#star"/></svg><svg viewBox="0 0 10 10"><use href="#star"/></svg><svg viewBox="0 0 10 10"><use href="#star"/></svg><svg viewBox="0 0 10 10"><use href="#star"/></svg></div><p>“Lorem ipsum dolor sit amet, consectetur adipiscing elit, sed do eiusmod tempor inc ididunt ut labore et dolore magna aliqua.”</p><p class="who">-R. Hale, Linden, GA</p></article>
</div>
<div class="t-row" style="top:2367px">
  <article class="card" style="left:-66px"><h4>Lorem ipsum dolor sit amet, consectetur</h4><div class="stars"><svg viewBox="0 0 10 10"><use href="#star"/></svg><svg viewBox="0 0 10 10"><use href="#star"/></svg><svg viewBox="0 0 10 10"><use href="#star"/></svg><svg viewBox="0 0 10 10"><use href="#star"/></svg><svg viewBox="0 0 10 10"><use href="#star"/></svg></div><p>“Lorem ipsum dolor sit amet, consectetur adipiscing elit, sed do eiusmod tempor inc ididunt ut labore et dolore magna aliqua.”</p><p class="who">-R. Hale, Linden, GA</p></article>
  <article class="card" style="left:276px"><h4>Lorem ipsum dolor sit amet, consectetur</h4><div class="stars"><svg viewBox="0 0 10 10"><use href="#star"/></svg><svg viewBox="0 0 10 10"><use href="#star"/></svg><svg viewBox="0 0 10 10"><use href="#star"/></svg><svg viewBox="0 0 10 10"><use href="#star"/></svg><svg viewBox="0 0 10 10"><use href="#star"/></svg></div><p>“Lorem ipsum dolor sit amet, consectetur adipiscing elit, sed do eiusmod tempor inc ididunt ut labore et dolore magna aliqua.”</p><p class="who">-R. Hale, Linden, GA</p></article>
  <article class="card" style="left:613px"><h4>Lorem ipsum dolor sit amet, consectetur</h4><div class="stars"><svg viewBox="0 0 10 10"><use href="#star"/></svg><svg viewBox="0 0 10 10"><use href="#star"/></svg><svg viewBox="0 0 10 10"><use href="#star"/></svg><svg viewBox="0 0 10 10"><use href="#star"/></svg><svg viewBox="0 0 10 10"><use href="#star"/></svg></div><p>“Lorem ipsum dolor sit amet, consectetur adipiscing elit, sed do eiusmod tempor inc ididunt ut labore et dolore magna aliqua.”</p><p class="who">-R. Hale, Linden, GA</p></article>
  <article class="card" style="left:950px"><h4>Lorem ipsum dolor sit amet, consectetur</h4><div class="stars"><svg viewBox="0 0 10 10"><use href="#star"/></svg><svg viewBox="0 0 10 10"><use href="#star"/></svg><svg viewBox="0 0 10 10"><use href="#star"/></svg><svg viewBox="0 0 10 10"><use href="#star"/></svg><svg viewBox="0 0 10 10"><use href="#star"/></svg></div><p>“Lorem ipsum dolor sit amet, consectetur adipiscing elit, sed do eiusmod tempor inc ididunt ut labore et dolore magna aliqua.”</p><p class="who">-R. Hale, Linden, GA</p></article>
</div>

<h2 class="wrap left-title h" style="top:2740px">Real Experiences. Real Memories.</h2>
<p class="wrap left-copy" style="top:2814px">PeakRoamJourneys is a comprehensive supplier of premier international sports travel and high-end event services.<br>We open the doors to the most exclusive events around the world</p>
<div class="g" role="img" aria-label="Overhead view of a basketball player dunking at the hoop" style="left:113px;top:2907px;width:313px;height:352px;background:linear-gradient(160deg,#8f9aa3 0%,#6d7a82 60%,#9aa4aa 100%)"></div>
<div class="g" role="img" aria-label="Youth basketball game in an indoor gym" style="left:445px;top:2907px;width:313px;height:168px;background:linear-gradient(180deg,#c08a5a 0%,#b77a48 100%)"></div>
<div class="g" role="img" aria-label="Two footballers contesting the ball on grass" style="left:445px;top:3091px;width:313px;height:168px;background:linear-gradient(180deg,#c9b07a 0%,#4f8a3c 60%,#3f7a2f 100%)"></div>
<div class="g" role="img" aria-label="Sprinter launching from starting blocks on a track" style="left:776px;top:2907px;width:313px;height:352px;background:linear-gradient(180deg,#c7b84e 0%,#6a6a4a 35%,#3e4750 100%)"></div>
<span class="btn" style="position:absolute;left:528px;top:3294px;height:36px;font-size:14px"><svg viewBox="0 0 12 12" fill="none" stroke="currentColor" stroke-width="2"><path d="M1 1l5 5-5 5M6 1l5 5-5 5"/></svg>View Gallery</span>

<div class="rule" style="top:3412px"></div>

<h2 class="center-title h" style="top:3490px">Frequently Asked Questions</h2>
<p class="center-copy" style="top:3565px">PeakRoamJourneys is a comprehensive supplier of premier international sports travel and high-end event services.<br>We open the doors to the most exclusive events around the world</p>

<div class="faq" style="left:112px;top:3662px">Lorem ipsum dolor sit amet, consectetur adipis<svg viewBox="0 0 12 8" fill="none" stroke="#1d1d2b" stroke-width="2"><path d="M1 1l5 5 5-5"/></svg></div>
<div class="faq" style="left:112px;top:3724px">Lorem ipsum dolor sit amet, consectetur adipis<svg viewBox="0 0 12 8" fill="none" stroke="#1d1d2b" stroke-width="2"><path d="M1 1l5 5 5-5"/></svg></div>
<div class="faq" style="left:112px;top:3786px">Lorem ipsum dolor sit amet, consectetur adipis<svg viewBox="0 0 12 8" fill="none" stroke="#1d1d2b" stroke-width="2"><path d="M1 1l5 5 5-5"/></svg></div>
<div class="faq" style="left:112px;top:3848px">Lorem ipsum dolor sit amet, consectetur adipis<svg viewBox="0 0 12 8" fill="none" stroke="#1d1d2b" stroke-width="2"><path d="M1 1l5 5 5-5"/></svg></div>
<div class="faq" style="left:112px;top:3910px">Lorem ipsum dolor sit amet, consectetur adipis<svg viewBox="0 0 12 8" fill="none" stroke="#1d1d2b" stroke-width="2"><path d="M1 1l5 5 5-5"/></svg></div>
<div class="faq" style="left:615px;top:3662px">Lorem ipsum dolor sit amet, consectetur adipis<svg viewBox="0 0 12 8" fill="none" stroke="#1d1d2b" stroke-width="2"><path d="M1 1l5 5 5-5"/></svg></div>
<div class="faq" style="left:615px;top:3724px">Lorem ipsum dolor sit amet, consectetur adipis<svg viewBox="0 0 12 8" fill="none" stroke="#1d1d2b" stroke-width="2"><path d="M1 1l5 5 5-5"/></svg></div>
<div class="faq" style="left:615px;top:3786px">Lorem ipsum dolor sit amet, consectetur adipis<svg viewBox="0 0 12 8" fill="none" stroke="#1d1d2b" stroke-width="2"><path d="M1 1l5 5 5-5"/></svg></div>
<div class="faq" style="left:615px;top:3848px">Lorem ipsum dolor sit amet, consectetur adipis<svg viewBox="0 0 12 8" fill="none" stroke="#1d1d2b" stroke-width="2"><path d="M1 1l5 5 5-5"/></svg></div>

<div class="band" style="top:4035px;height:665px"></div>
<h2 class="wrap left-title h" style="top:4112px">Contact Us</h2>
<p class="wrap left-copy" style="top:4190px">PeakRoamJourneys is a comprehensive supplier of premier international sports travel and high-end event services.<br>We open the doors to the most exclusive events around the world</p>

<div class="field" style="top:4285px">Name</div>
<div class="field" style="top:4339px">Email Address</div>
<div class="field" style="top:4393px">Phone Number</div>
<div class="field" style="top:4447px;height:110px">Message Us</div>
<span class="btn" style="position:absolute;left:112px;top:4578px;height:36px;font-size:15px"><svg viewBox="0 0 12 12" fill="none" stroke="currentColor" stroke-width="2"><path d="M1 1l5 5-5 5M6 1l5 5-5 5"/></svg>Submit</span>

<div class="info" style="top:4283px"><b>Address</b><span>14, Lorem ipsum dolor sit amet, conse ctetur adipiscing elit,</span></div>
<div class="info" style="top:4336px"><b>Phone</b><span>+1 555 010 0199</span></div>
<div class="info" style="top:4364px"><b>Email</b><span>info@peakroamjourneys.example</span></div>
<div class="g" role="img" aria-label="Street map showing the office location with a pin" style="left:657px;top:4408px;width:432px;height:212px;background:linear-gradient(135deg,#d9dbe0 0%,#e4e6ea 50%,#cfd3da 100%)"></div>

<footer class="site-footer">
  <div class="brand-f h">PeakRoamJourneys</div>
  <nav class="foot-nav"><span>Home</span><span>About</span><span>Sports Travel Products</span><span>Reviews</span><span>News</span><span>Contact Us</span></nav>
  <div class="foot-rule"></div>
  <p class="copy">Copyright © 2025 PeakRoamJourneys. All rights reserved.</p>
</footer>

</body>
</html>
```